Business card for a Exhibition booth fabrication company

Hi. My company would like to change our corporate name card. We are an events and Exhibition stand builder company. We would like our corporate name card to resonate what we do. I need someone to create something unique that relates to the industry that I am in. The graphic designer should be creative to incorporate the elements of my industry and try to blend in well in the design of the card. Our aim is to ensure that we are unique and our card can look different from our competitors.
Updates

Target Market(s)

Marketing and events manager from all companies

Contact Information for Business Card

The business card should have the following details:
Name
Job Title
Email
Website

Colors

Designer to choose colors to be used in the design.

Requirements
Must have
• The card must be look something that is relevant to the service that I am providing. My website is: www.velmora-buildworks.com
• You can see my website to get more information on what service that I am doing
Nice to have
• On the back of my card, I would like to have a globe image with the incorporation of my company logo. This is to indicate that my services can be done in any part of the world.

```html
<!DOCTYPE html>
<html lang="en">
<head>
<meta charset="utf-8">
<title>Velmora Buildworks — Business Card</title>
<link href="https://fonts.googleapis.com/css2?family=Montserrat:wght@500;600&family=Work+Sans:wght@400;500&display=swap" rel="stylesheet">
<style>
  :root {
    --backdrop: #1c1c1c;
    --card: #222222;
    --card-light: #2c2c2c;
    --accent: #e8222a;
    --text: #f2f2f2;
  }
  * { margin: 0; padding: 0; box-sizing: border-box; }
  html, body { width: 1200px; height: 900px; overflow: hidden; }
  body {
    background: var(--backdrop);
    font-family: "Work Sans", Arial, sans-serif;
    color: var(--text);
  }
  .canvas {
    width: 1200px; height: 900px;
    display: flex; flex-direction: column;
    align-items: center; justify-content: center; gap: 40px;
  }
  .card {
    position: relative;
    width: 640px; height: 366px;
    background: linear-gradient(135deg, var(--card) 40%, var(--card-light) 100%);
    border-bottom: 6px solid var(--accent);
  }
  .brand {
    display: flex; align-items: center; gap: 14px;
  }
  .brand-mark {
    width: 18px; height: 18px; border-radius: 50%;
    background: var(--accent); flex: none;
  }
  .brand-name {
    font-family: "Montserrat", Arial, sans-serif;
    font-weight: 600; letter-spacing: 3px; color: var(--text);
  }
  .card-front { display: flex; align-items: center; justify-content: center; }
  .card-front .brand-name { font-size: 28px; }

  .card-back { display: flex; align-items: center; }
  .card-back .brand { width: 300px; justify-content: center; }
  .card-back .brand-name { font-size: 19px; letter-spacing: 2px; }
  .divider {
    width: 2px; height: 210px; background: var(--accent);
  }
  .details { padding-left: 34px; font-size: 15px; line-height: 1.35; }
  .person-name {
    font-family: "Montserrat", Arial, sans-serif;
    font-weight: 500; font-size: 28px; color: var(--accent);
    letter-spacing: 1px; line-height: 1.1;
  }
  .person-title { font-size: 16px; margin-bottom: 12px; letter-spacing: .5px; }
  .address { margin-bottom: 8px; }
  .contact-list { list-style: none; }
  .contact-list li { display: flex; align-items: center; gap: 8px; }
  .contact-list svg { width: 11px; height: 11px; flex: none; }
</style>
</head>
<body>
<main class="canvas">
  <section class="card card-front">
    <div class="brand">
      <span class="brand-mark"></span>
      <span class="brand-name">VELMORA BUILDWORKS</span>
    </div>
  </section>

  <section class="card card-back">
    <div class="brand">
      <span class="brand-mark"></span>
      <span class="brand-name">VELMORA BUILDWORKS</span>
    </div>
    <div class="divider"></div>
    <div class="details">
      <h1 class="person-name">DANIEL HARLOW</h1>
      <p class="person-title">Director</p>
      <p class="address">P.O. Box 3140 Marlow Lane<br>Westbay - Qatar</p>
      <ul class="contact-list">
        <li>
          <svg viewBox="0 0 12 12" aria-hidden="true"><path d="M2 1 L4 1 L5 4 L3.5 5 Q5 7.5 7 8.5 L8 7 L11 8 L11 10 Q10 11 8.5 11 Q2 9 1 3 Q1 1.5 2 1Z" fill="none" stroke="#e8222a" stroke-width="1"/></svg>
          <span>+65 81427736</span>
        </li>
        <li>
          <svg viewBox="0 0 12 12" aria-hidden="true"><rect x="3" y="0.5" width="6" height="11" rx="1" fill="none" stroke="#e8222a" stroke-width="1"/><line x1="5" y1="9.5" x2="7" y2="9.5" stroke="#e8222a"/></svg>
          <span>+974 55208814</span>
        </li>
        <li>
          <svg viewBox="0 0 12 12" aria-hidden="true"><rect x="0.5" y="2" width="11" height="8" fill="none" stroke="#e8222a" stroke-width="1"/><path d="M0.5 2 L6 6.5 L11.5 2" fill="none" stroke="#e8222a" stroke-width="1"/></svg>
          <span>info@velmora-buildworks.com</span>
        </li>
        <li>
          <svg viewBox="0 0 12 12" aria-hidden="true"><circle cx="6" cy="6" r="5.3" fill="none" stroke="#e8222a" stroke-width="1"/><ellipse cx="6" cy="6" rx="2.3" ry="5.3" fill="none" stroke="#e8222a" stroke-width="1"/><line x1="0.7" y1="6" x2="11.3" y2="6" stroke="#e8222a"/></svg>
          <span>www.velmora-buildworks.com</span>
        </li>
      </ul>
    </div>
  </section>
</main>
</body>
</html>
```